Tinker's Lamp sports bar beer & food menu

We need a menu design for our gastropub sports bar in L.A.'s Sawtelle Neighborhood (Little Osaka). We have a full-bar (hard liquor, craft beer, wine and cocktails) . We have a lunch and dinner menu as well as a happy hour menu. On Sundays we have a seperate menu with brunch items. The design concept is a British pub type of sports bar. We're looking for something different from our existing menu design. Ideally something cleaner and more legible. It should mesh a simple, modern sensibility with the more traditional darkened pub style of our interior design.

You can check out our Voxly page for photos of the interior/exterior:
https://www.reviewhatch.example/biz_photos/tinkers-lamp-los-angeles?tab=interior

You can view our existing menu here:
https://www.reviewhatch.example/biz_photos/tinkers-lamp-los-angeles?tab=menu

If there's an area of the design that can be a little more playful it's our highlighted event schedule so that the events will stand out.

Target Market(s)

Age of 25 and up. Sawtelle is a cultural hub that caters to a younger, moderately affluent crowd.

Industry/Entity Type

Sports Bar

Font styles to use
Sans Serif

Colors

Designer to choose colors to be used in the design.

Requirements
Must have
• Logo, highlighted event schedule (beer pong Monday, trivia Tuesday, taco Tuesday, whiskey Wednesday, karaoke Saturday). The menu should be easy to read in a darkened bar. We'll be printing on standard 8.5x11 in portrait.
Nice to have
• We're trying to have the menu take up as few pages as possible.
Should not have
• We're trying to have the menu take up as few pages as possible. Food photography isn't necessary. A cover isn't necessary. Please avoid clip art of food.

```html
<!DOCTYPE html>
<html lang="en">
<head>
<meta charset="utf-8">
<title>Tinker's Lamp — Pub Menu</title>
<link rel="stylesheet" href="https://fonts.googleapis.com/css2?family=Bebas+Neue&family=Open+Sans:wght@400&family=Kaushan+Script&display=swap">
<style>
  :root {
    --gold: #c8953f;
    --ink: #050505;
    --panel: #0a0a0a;
    --brick-light: #4a4a4a;
    --brick-dark: #1e1e1e;
    --white: #ffffff;
    --paper: #ffffff;
    --addon-bg: #2f2f2f;
    --frame: #3b3b3b;
    --frame-edge: #6a6a6a;
  }
  * { margin: 0; padding: 0; box-sizing: border-box; }
  html, body { width: 1200px; height: 847px; overflow: hidden; background: #222; }
  .menu-sheet { position: relative; width: 1200px; height: 847px; overflow: hidden; }

  .brick-wall {
    position: absolute; inset: 0;
    background: radial-gradient(ellipse at 50% 40%, var(--brick-light), var(--brick-dark) 80%);
  }
  .fold-line { position: absolute; top: 0; bottom: 0; width: 1px; background: rgba(0,0,0,.55); }

  .cover-shapes { position: absolute; left: 282px; top: 0; width: 318px; height: 847px; }

  .menu-board { position: absolute; background: var(--panel); color: var(--white); }
  .section-title {
    position: absolute; white-space: nowrap;
    font-family: "Bebas Neue", sans-serif; font-weight: 400;
    font-size: 21px; line-height: 22px;
    color: var(--gold); text-transform: uppercase;
  }
  .side-list { position: absolute; list-style: none; }
  .side-list li {
    display: flex; justify-content: space-between;
    font-family: "Bebas Neue", sans-serif; font-size: 14.5px; line-height: 13.8px;
    text-transform: uppercase;
  }
  .side-list .price { color: var(--gold); font-size: 11px; }

  .dish-list { position: absolute; top: 0; bottom: 0; list-style: none; }
  .dish {
    position: absolute; left: 0; right: 0; padding-right: 28px;
    font-family: "Open Sans", sans-serif; font-size: 7px; line-height: 10px;
  }
  .dish-name {
    font-family: "Bebas Neue", sans-serif; font-size: 13.5px; line-height: 10px;
    text-transform: uppercase; color: var(--white);
  }
  .dish-name::after { content: ":"; color: var(--gold); }
  .dish .price {
    position: absolute; right: 0; top: 0;
    font-family: "Bebas Neue", sans-serif; font-size: 11px; line-height: 10px; color: var(--gold);
  }

  .add-ons {
    position: absolute; left: 105px; top: 461px; width: 77px; height: 77px;
    background: var(--addon-bg); color: var(--white); padding: 4px 0 0 8px;
    font-family: "Bebas Neue", sans-serif;
  }
  .add-ons h3 { font-weight: 400; font-size: 14px; line-height: 16px; margin-bottom: 2px; }
  .add-ons ul { list-style: none; padding-left: 4px; }
  .add-ons li { font-size: 10.5px; line-height: 13px; display: flex; align-items: center; }
  .add-ons li::before { content: ""; width: 2px; height: 2px; background: var(--gold); margin-right: 3px; }
  .add-ons .label { width: 38px; }
  .add-ons .price { color: var(--gold); }

  .wall-frame {
    position: absolute; background: var(--frame);
    border: 2px solid var(--frame-edge);
    box-shadow: inset 0 0 0 6px #2a2a2a, 0 4px 10px rgba(0,0,0,.6);
  }
  .contact-board {
    position: absolute; left: 42px; top: 630px; width: 201px; height: 154px;
    background: var(--ink); color: var(--white); font-family: "Bebas Neue", sans-serif;
  }
  .contact-board h3 { position: absolute; left: 8px; top: 6px; font-weight: 400; font-size: 14px; }
  .contact-list { list-style: none; position: absolute; left: 15px; top: 32px; }
  .contact-list li { display: flex; align-items: center; height: 30px; font-size: 11px; }
  .contact-icon { width: 13px; height: 13px; margin-right: 6px; flex: none; }

  .brand-mark {
    position: absolute; left: 530px; top: 650px;
    transform: translate(-50%, -50%) rotate(-90deg);
    font-family: "Bebas Neue", sans-serif; font-weight: 400;
    font-size: 54px; line-height: 1; color: var(--ink); white-space: nowrap;
  }

  .events-board {
    position: absolute; left: 952px; top: 502px; width: 200px; height: 295px;
    background: var(--gold); text-align: center; color: #141414;
    font-family: "Kaushan Script", cursive;
  }
  .events-board h2 { font-weight: 400; font-size: 29px; line-height: 1; margin-top: 20px; margin-bottom: 28px; }
  .events-board ul { list-style: none; }
  .events-board li { font-size: 22px; line-height: 41px; }
</style>
</head>
<body>
<main class="menu-sheet">
  <div class="brick-wall" role="img" aria-label="Dark brick wall texture"></div>
  <span class="fold-line" style="left:282px"></span>
  <span class="fold-line" style="left:600px"></span>
  <span class="fold-line" style="left:900px"></span>

  <svg class="cover-shapes" viewBox="0 0 318 847" aria-hidden="true">
    <polygon points="318,10 318,235 0,790 0,564" fill="var(--gold)"/>
    <polygon points="318,235 318,847 0,847 0,790" fill="var(--paper)"/>
  </svg>
  <div class="brand-mark">Tinker's Lamp</div>

  <!-- Left panel: sides, desserts, salads -->
  <section class="menu-board" style="left:17px;top:24px;width:250px;height:541px">
    <h2 class="section-title" style="left:-12px;top:5px">Sides</h2>
    <ul class="side-list" style="left:10px;top:34px;width:225px">
      <li><span>House Fries</span><span class="price">12</span></li>
      <li><span>Truffle Fries</span><span class="price">13</span></li>
      <li><span>Dry Rub Fries</span><span class="price">13</span></li>
      <li><span>Sweet Potato Fries</span><span class="price">10</span></li>
    </ul>

    <h2 class="section-title" style="left:-11px;top:108px">Desserts</h2>
    <ul class="side-list" style="left:10px;top:133px;width:225px">
      <li><span>House Fries</span><span class="price">12</span></li>
      <li><span>Truffle Fries</span><span class="price">13</span></li>
      <li><span>Dry Rub Fries</span><span class="price">13</span></li>
    </ul>

    <h2 class="section-title" style="left:-8px;top:184px">Salad and Soups</h2>
    <ul class="dish-list" style="left:9px;width:224px">
      <li class="dish" style="top:213px"><span class="dish-name">Chicken Sandwich</span> Chicken Breast, Applewood Bacon, Butter Lettuce, White Cheddar, Avocado and Tomato Served on Sourdough Bread.<span class="price">12</span></li>
      <li class="dish" style="top:253px"><span class="dish-name">Buttermilk Fried Chicken</span> Coleslaw, Provolone, Tomato, and a Spiced Mayonnaise on a Pretzel Roll<span class="price">13</span></li>
      <li class="dish" style="top:282px"><span class="dish-name">Short Rib Sandwich</span> Beef Shorts, Mayo, Tomato, Caramelized Onions, Arugula, Pepper Jack Cheese Served on Sourdough Bread<span class="price">13</span></li>
      <li class="dish" style="top:323px"><span class="dish-name">Grilled Cheese Sandwich</span> Cheese, Provolone and Cheddar Cheese<span class="price">10</span></li>
      <li class="dish" style="top:352px"><span class="dish-name">Tinker's Lamp Burger</span> Sharp Cheddar, Arugula, Roasted Shallots, Bacon Jam with Malt Aioli<span class="price">14</span></li>
      <li class="dish" style="top:380px"><span class="dish-name">The Truffle Burger</span> Caramelized Onions, Arugula, Truffle Pecorino, Truffle Mayo and Truffle Fries<span class="price">15</span></li>
      <li class="dish" style="top:408px"><span class="dish-name">The Sloppy Joe</span> Shredded Lettuce and Sharp Cheddar<span class="price">10</span></li>
    </ul>
  </section>

  <aside class="add-ons">
    <h3>ADD ONS:</h3>
    <ul>
      <li><span class="label">CHICKEN</span><span class="price">4</span></li>
      <li><span class="label">SHRIMP</span><span class="price">6</span></li>
      <li><span class="label">SALMON</span><span class="price">6</span></li>
      <li><span class="label">STEAK</span><span class="price">9</span></li>
    </ul>
  </aside>

  <div class="wall-frame" style="left:24px;top:609px;width:240px;height:198px"></div>
  <section class="contact-board">
    <h3>FIND US:</h3>
    <ul class="contact-list">
      <li>
        <svg class="contact-icon" viewBox="0 0 20 20" aria-hidden="true"><circle cx="10" cy="10" r="10" fill="var(--gold)"/><path d="M6.5 5.5l2 0 1 3-1.3 1c.6 1.3 1.5 2.2 2.8 2.8l1-1.3 3 1v2c0 .6-.5 1-1 1C9 15 5 11 5 6.5c0-.5.4-1 1-1z" fill="#111"/></svg>
        987-TINKERS
      </li>
      <li>
        <svg class="contact-icon" viewBox="0 0 20 20" aria-hidden="true"><rect width="20" height="20" rx="3" fill="var(--gold)"/></svg>
        TINKERSLAMP
      </li>
      <li>
        <svg class="contact-icon" viewBox="0 0 20 20" aria-hidden="true"><circle cx="10" cy="10" r="10" fill="var(--gold)"/></svg>
        @TINKERSLAMP
      </li>
      <li>
        <svg class="contact-icon" viewBox="0 0 20 20" aria-hidden="true" fill="none" stroke="var(--gold)" stroke-width="1.4"><circle cx="10" cy="10" r="8.5"/><ellipse cx="10" cy="10" rx="3.8" ry="8.5"/><path d="M1.5 10h17M3 5.5h14M3 14.5h14"/></svg>
        WWW.TINKERSLAMP.EXAMPLE
      </li>
    </ul>
  </section>

  <!-- Inside panel: burgers, bites, flatbreads -->
  <section class="menu-board" style="left:626px;top:24px;width:250px;height:796px">
    <h2 class="section-title" style="left:-17px;top:7px">Burgers and Sandwiches</h2>
    <ul class="dish-list" style="left:9px;width:228px">
      <li class="dish" style="top:38px"><span class="dish-name">Chicken Sandwich</span> Chicken Breast, Applewood Bacon, Butter Lettuce, White Cheddar, Avocado and Tomato Served on Sourdough Bread.<span class="price">12</span></li>
      <li class="dish" style="top:78px"><span class="dish-name">Buttermilk Fried Chicken</span> Coleslaw, Provolone, Tomato, and a Spiced Mayonnaise on a Pretzel Roll<span class="price">13</span></li>
      <li class="dish" style="top:108px"><span class="dish-name">Short Rib Sandwich</span> Beef Shorts, Mayo, Tomato, Caramelized Onions, Arugula, Pepper Jack Cheese Served on Sourdough Bread<span class="price">13</span></li>
      <li class="dish" style="top:148px"><span class="dish-name">Grilled Cheese Sandwich</span> Cheese, Provolone and Cheddar Cheese<span class="price">10</span></li>
      <li class="dish" style="top:177px"><span class="dish-name">Tinker's Lamp Burger</span> Sharp Cheddar, Arugula, Roasted Shallots, Bacon Jam with Malt Aioli<span class="price">14</span></li>
      <li class="dish" style="top:205px"><span class="dish-name">The Truffle Burger</span> Caramelized Onions, Arugula, Truffle Pecorino, Truffle Mayo and Truffle Fries<span class="price">15</span></li>
      <li class="dish" style="top:234px"><span class="dish-name">The Sloppy Joe</span> Shredded Lettuce and Sharp Cheddar<span class="price">10</span></li>
      <li class="dish" style="top:251px"><span class="dish-name">Veggie Burger</span> Concoction of kale, Tomato, Avocado, Sharp Cheddar with a Balsamic Reduction<span class="price">12</span></li>
      <li class="dish" style="top:282px"><span class="dish-name">Flat Iron Steak Sandwich</span> Arugula, Peppers, Fontina, Onion and Mayo<span class="price">16</span></li>
      <li class="dish" style="top:308px"><span class="dish-name">Chicken Spinach Wrap</span> Chicken, Bacon, Lettuce, Tomato, Avocado, Ranch and Mayo<span class="price">10</span></li>
      <li class="dish" style="top:334px"><span class="dish-name">Fried Chicken Sliders</span> Coleslaw, Lime Sriracha Sauce<span class="price">12</span></li>
    </ul>

    <h2 class="section-title" style="left:-16px;top:362px">Big Dog Bites</h2>
    <ul class="dish-list" style="left:6px;width:228px">
      <li class="dish" style="top:393px"><span class="dish-name">Chicken Sandwich</span> Chicken Breast, Applewood Bacon, Butter Lettuce, White Cheddar, Avocado and Tomato Served on Sourdough Bread.<span class="price">12</span></li>
      <li class="dish" style="top:433px"><span class="dish-name">Buttermilk Fried Chicken</span> Coleslaw, Provolone, Tomato, and a Spiced Mayonnaise on a Pretzel Roll<span class="price">13</span></li>
      <li class="dish" style="top:463px"><span class="dish-name">Short Rib Sandwich</span> Beef Shorts, Mayo, Tomato, Caramelized Onions, Arugula, Pepper Jack Cheese Served on Sourdough Bread<span class="price">13</span></li>
      <li class="dish" style="top:502px"><span class="dish-name">Grilled Cheese Sandwich</span> Cheese, Provolone and Cheddar Cheese<span class="price">10</span></li>
      <li class="dish" style="top:532px"><span class="dish-name">Tinker's Lamp Burger</span> Sharp Cheddar, Arugula, Roasted Shallots, Bacon Jam with Malt Aioli<span class="price">14</span></li>
    </ul>

    <h2 class="section-title" style="left:-14px;top:573px">Flatbreads</h2>
    <ul class="dish-list" style="left:7px;width:228px">
      <li class="dish" style="top:605px"><span class="dish-name">Chicken Sandwich</span> Chicken Breast, Applewood Bacon, Butter Lettuce, White Cheddar, Avocado and Tomato Served on Sourdough Bread.<span class="price">12</span></li>
      <li class="dish" style="top:645px"><span class="dish-name">Buttermilk Fried Chicken</span> Coleslaw, Provolone, Tomato, and a Spiced Mayonnaise on a Pretzel Roll<span class="price">13</span></li>
      <li class="dish" style="top:674px"><span class="dish-name">Short Rib Sandwich</span> Beef Shorts, Mayo, Tomato, Caramelized Onions, Arugula, Pepper Jack Cheese Served on Sourdough Bread<span class="price">13</span></li>
      <li class="dish" style="top:715px"><span class="dish-name">Grilled Cheese Sandwich</span> Cheese, Provolone and Cheddar Cheese<span class="price">10</span></li>
      <li class="dish" style="top:744px"><span class="dish-name">Tinker's Lamp Burger</span> Sharp Cheddar, Arugula, Roasted Shallots, Bacon Jam with Malt Aioli<span class="price">14</span></li>
      <li class="dish" style="top:772px"><span class="dish-name">The Truffle Burger</span> Caramelized Onions, Arugula, Truffle Pecorino, Truffle Mayo and Truffle Fries<span class="price">15</span></li>
    </ul>
  </section>

  <!-- Right panel: for the table, events -->
  <section class="menu-board" style="left:925px;top:24px;width:244px;height:318px">
    <h2 class="section-title" style="left:12px;top:10px">For the Table</h2>
    <ul class="dish-list" style="left:14px;width:224px">
      <li class="dish" style="top:38px"><span class="dish-name">Chicken Sandwich</span> Chicken Breast, Applewood Bacon, Butter Lettuce, White Cheddar, Avocado and Tomato Served on Sourdough Bread.<span class="price">12</span></li>
      <li class="dish" style="top:78px"><span class="dish-name">Buttermilk Fried Chicken</span> Coleslaw, Provolone, Tomato, and a Spiced Mayonnaise on a Pretzel Roll<span class="price">13</span></li>
      <li class="dish" style="top:108px"><span class="dish-name">Short Rib Sandwich</span> Beef Shorts, Mayo, Tomato, Caramelized Onions, Arugula, Pepper Jack Cheese Served on Sourdough Bread<span class="price">13</span></li>
      <li class="dish" style="top:148px"><span class="dish-name">Grilled Cheese Sandwich</span> Cheese, Provolone and Cheddar Cheese<span class="price">10</span></li>
      <li class="dish" style="top:177px"><span class="dish-name">Tinker's Lamp Burger</span> Sharp Cheddar, Arugula, Roasted Shallots, Bacon Jam with Malt Aioli<span class="price">14</span></li>
      <li class="dish" style="top:205px"><span class="dish-name">The Truffle Burger</span> Caramelized Onions, Arugula, Truffle Pecorino, Truffle Mayo and Truffle Fries<span class="price">15</span></li>
      <li class="dish" style="top:234px"><span class="dish-name">The Sloppy Joe</span> Shredded Lettuce and Sharp Cheddar<span class="price">10</span></li>
      <li class="dish" style="top:251px"><span class="dish-name">Veggie Burger</span> Concoction of kale, Tomato, Avocado, Sharp Cheddar with a Balsamic Reduction<span class="price">12</span></li>
      <li class="dish" style="top:282px"><span class="dish-name">Flat Iron Steak Sandwich</span> Arugula, Peppers, Fontina, Onion and Mayo<span class="price">16</span></li>
    </ul>
  </section>

  <div class="wall-frame" style="left:925px;top:473px;width:253px;height:350px"></div>
  <section class="events-board">
    <h2>Events Schedule</h2>
    <ul>
      <li>Beer pong Monday</li>
      <li>Trivia Tuesday</li>
      <li>Taco Tuesday</li>
      <li>Whiskey Wednesday</li>
      <li>Karaoke Saturday</li>
    </ul>
  </section>
</main>
</body>
</html>
```